New Company Business Card design

Looking for a corporate looking business card utilising my new logo design - the logo i would like embossed as one option and flat as another - simplistic but stylish - less is more - we are an import export business launching into the market - i would like a couple of options as main background - Grey or Black

```html
<!DOCTYPE html>
<html lang="en">
<head>
<meta charset="utf-8">
<title>Northgate Trade Partners – Business Card</title>
<link rel="stylesheet" href="https://fonts.googleapis.com/css2?family=Roboto:wght@400;500;700&family=Cinzel:wght@400;600&display=swap">
<style>
  :root {
    --backdrop: #e9e4dd;
    --card-grey: #5b5c60;
    --card-white: #f7f7f5;
    --brand-blue: #1f7fcf;
    --text-grey: #5d5f63;
    --rule-white: #ffffff;
    --circle-grey: #8e9094;
  }
  * { box-sizing: border-box; margin: 0; padding: 0; }
  html, body { width: 1200px; height: 848px; overflow: hidden; }
  body {
    background: var(--backdrop);
    display: flex;
    flex-direction: column;
    align-items: center;
    justify-content: center;
    gap: 40px;
    font-family: "Roboto", Arial, sans-serif;
  }
  .card {
    width: 630px;
    height: 360px;
    position: relative;
    box-shadow: 0 2px 8px rgba(0,0,0,0.12);
  }
  /* Front */
  .card-front {
    background: var(--card-grey);
    display: flex;
    flex-direction: column;
    align-items: center;
    justify-content: center;
    padding-bottom: 20px;
  }
  .front-mark {
    display: flex;
    align-items: center;
    gap: 12px;
  }
  .mark-circle {
    width: 22px; height: 22px;
    border-radius: 50%;
    background: var(--brand-blue);
    flex: none;
  }
  .front-name {
    font-weight: 500;
    font-size: 29px;
    letter-spacing: 2px;
    color: var(--brand-blue);
    text-transform: uppercase;
    white-space: nowrap;
  }
  .front-rule {
    width: 480px;
    height: 2px;
    background: var(--rule-white);
    margin: 12px 0 8px;
  }
  .tagline {
    font-family: "Cinzel", Georgia, serif;
    font-size: 13px;
    letter-spacing: 3px;
    color: var(--rule-white);
    text-transform: uppercase;
    white-space: nowrap;
  }
  /* Back */
  .card-back {
    background: var(--card-white);
    padding: 0 34px 0 44px;
    display: flex;
    align-items: center;
    justify-content: space-between;
  }
  .back-mark {
    display: flex;
    align-items: center;
    gap: 12px;
    margin-bottom: 60px;
  }
  .back-mark .mark-circle { background: var(--circle-grey); }
  .back-name {
    font-weight: 500;
    font-size: 30px;
    letter-spacing: 1px;
    color: var(--brand-blue);
    text-transform: uppercase;
  }
  .contact {
    text-align: right;
    color: var(--text-grey);
    font-size: 14px;
    line-height: 1.35;
    margin-top: 36px;
  }
  .person-name {
    color: var(--brand-blue);
    font-weight: 700;
    font-size: 18px;
    letter-spacing: 0.5px;
  }
  .person-role { margin-bottom: 10px; }
  .address { margin-bottom: 6px; }
  .line {
    display: flex;
    justify-content: flex-end;
    align-items: center;
    gap: 8px;
    white-space: nowrap;
  }
  .line svg { width: 12px; height: 12px; fill: var(--brand-blue); flex: none; }
  .line .spacer { width: 12px; flex: none; }
</style>
</head>
<body>
  <section class="card card-front">
    <div class="front-mark">
      <span class="mark-circle"></span>
      <span class="front-name">Northgate Trade Partners</span>
    </div>
    <div class="front-rule"></div>
    <p class="tagline">Worldwide supply for regional demand</p>
  </section>

  <section class="card card-back">
    <div class="back-mark">
      <span class="mark-circle"></span>
      <span class="back-name">Northgate</span>
    </div>
    <div class="contact">
      <p class="person-name">DANIEL HART</p>
      <p class="person-role">CEO/FOUNDER</p>
      <div class="address">
        <p class="line">412 Harbor View Road<span class="spacer"></span></p>
        <p class="line">Juneau, Alaska 99801<span class="spacer"></span></p>
      </div>
      <p class="line">907 555 0142
        <svg viewBox="0 0 24 24" aria-label="phone"><path d="M6.6 10.8a15 15 0 0 0 6.6 6.6l2.2-2.2c.3-.3.7-.4 1-.2 1.1.4 2.3.6 3.6.6.6 0 1 .4 1 1V20c0 .6-.4 1-1 1A17 17 0 0 1 3 4c0-.6.4-1 1-1h3.5c.6 0 1 .4 1 1 0 1.3.2 2.5.6 3.6.1.3 0 .7-.2 1z"/></svg></p>
      <p class="line">907 555 0187
        <svg viewBox="0 0 24 24" aria-label="mobile"><path d="M7 1h10a2 2 0 0 1 2 2v18a2 2 0 0 1-2 2H7a2 2 0 0 1-2-2V3a2 2 0 0 1 2-2zm0 3v15h10V4zm5 16.2a.9.9 0 1 0 0 1.8.9.9 0 0 0 0-1.8z"/></svg></p>
      <p class="line">907 555 0163
        <svg viewBox="0 0 24 24" aria-label="fax"><path d="M6 2h10l2 2v5H6zM3 10h18a1 1 0 0 1 1 1v8a1 1 0 0 1-1 1H3a1 1 0 0 1-1-1v-8a1 1 0 0 1 1-1zm3 5v6h12v-6z"/></svg></p>
      <p class="line">hello@northgatetrade.com
        <svg viewBox="0 0 24 24" aria-label="email"><path d="M2 5h20v14H2zm2 2v.5l8 5 8-5V7l-8 5z"/></svg></p>
      <p class="line">www.northgatetrade.com
        <svg viewBox="0 0 24 24" aria-label="website"><circle cx="12" cy="12" r="10"/></svg></p>
    </div>
  </section>
</body>
</html>
```